Website for a Pittsburgh Musical Production

We are creating a website for a musical stage production. Content and copy is included below. We are targeting production in early 2023.

```html
<!DOCTYPE html>
<html lang="en">
<head>
<meta charset="utf-8">
<title>Galvanica – The Rock Opera</title>
<link href="https://fonts.googleapis.com/css2?family=Open+Sans:wght@400;600;700;800&display=swap" rel="stylesheet">
<style>
:root{
  --bg:#1c2320;
  --hero:#2c2f29;
  --olive:#6c7a58;
  --olive-dark:#5d6a4b;
  --band:#6b7957;
  --white:#ffffff;
  --ink:#111111;
  --muted:#7d7d7d;
  --date:#6c7a58;
}
*{margin:0;padding:0;box-sizing:border-box}
html,body{width:1200px;height:3079px;overflow:hidden}
body{background:var(--bg);font-family:'Open Sans',sans-serif;color:var(--white);position:relative}
.abs{position:absolute}
.hero{left:0;top:0;width:1200px;height:650px;background:radial-gradient(ellipse at 45% 35%,#3a3e35 0%,var(--hero) 60%,#22251f 100%)}
.hero-edge{left:0;top:600px;width:1200px;height:60px}
.logo{font-family:'Open Sans',sans-serif;font-weight:800;font-size:27px;letter-spacing:1px;color:var(--white);text-transform:uppercase}
.nav{left:424px;top:42px;display:flex;gap:6px;align-items:center}
.nav a{font-size:14.5px;font-weight:700;color:var(--white);text-decoration:none;padding:8px 11px;text-transform:uppercase}
.nav a.active{background:var(--white);color:var(--olive);border-radius:6px}
.lang{left:1009px;top:45px;display:flex;align-items:center;gap:6px;font-size:14.5px;font-weight:700}
.lang .dot{width:28px;height:28px;border-radius:50%;background:#c9c9d6}
.face{left:330px;top:60px;width:230px;height:480px;border-radius:45% 40% 35% 50%;background:radial-gradient(ellipse at 55% 45%,#8fa86a 0%,#5e7046 35%,rgba(44,47,41,0) 75%);opacity:.75}
.lettering{left:578px;top:175px;width:318px;height:130px;background:linear-gradient(180deg,rgba(120,150,80,.55),rgba(90,110,60,.35));border-radius:8px}
.hero-text{left:577px;top:318px;width:445px;font-size:15px;line-height:22.5px}
.btn-green{left:575px;top:400px;width:153px;height:49px;border-radius:25px;background:var(--olive);color:var(--white);font-size:14.5px;font-weight:700;display:flex;align-items:center;justify-content:center;text-transform:uppercase}
.dots{left:583px;top:554px;display:flex;gap:5px}
.dots span{width:12px;height:12px;border-radius:50%;border:2px solid var(--white)}
.dots span:first-child{border-color:#888}
.card{width:310px;height:410px;background:var(--white);border:2px solid #d8d8d8;border-radius:6px;padding:3px;color:var(--ink);text-align:center}
.card .pic{height:180px;border-radius:2px}
.card h3{font-size:20px;font-weight:700;margin-top:24px;text-transform:uppercase}
.card p{font-size:14px;line-height:22.5px;color:var(--muted);margin:8px 18px 0}
.card .more{position:absolute;left:3px;right:3px;bottom:3px;height:55px;background:var(--olive);border-radius:2px;display:flex;align-items:center;justify-content:space-between;padding:0 18px 0 20px;color:var(--white);font-size:14px;font-weight:700}
.band{left:0;top:1238px;width:1200px;height:461px;background:linear-gradient(90deg,#6b7957,#717f5c 60%,#6b7957)}
.singer{left:644px;top:1217px;width:446px;height:505px;background:radial-gradient(ellipse at 40% 20%,#6d7ea3 0%,#2c3658 40%,#0e1222 85%)}
.about h2{font-size:34px;font-weight:700;text-transform:uppercase}
.about p{font-size:14.5px;line-height:22.5px;margin-top:10px;text-align:justify}
.btn-white{left:111px;top:1557px;width:153px;height:49px;border-radius:25px;background:var(--white);color:var(--olive);font-size:14.5px;font-weight:700;display:flex;align-items:center;justify-content:center;text-transform:uppercase}
.section-title{left:0;width:1200px;text-align:center;font-size:34px;font-weight:700;text-transform:uppercase}
.news{width:477px;height:233px;background:var(--white);padding:4px;display:flex;color:var(--ink)}
.news .pic{width:211px;height:225px;flex:none}
.news .body{padding:20px 20px 0 21px}
.news h4{font-size:21px;font-weight:600;line-height:28.5px}
.news .date{font-size:14px;font-weight:600;color:var(--date);margin-top:12px;display:flex;align-items:center;gap:6px}
.news p{font-size:14px;line-height:22.5px;color:var(--muted);margin-top:10px}
.strip{top:2537px;height:211px}
.arrow{top:2630px}
.footer-nav{left:0;top:2885px;width:1200px;display:flex;justify-content:center;gap:27px;font-size:14px;font-weight:600;text-transform:uppercase}
.social{left:0;top:2933px;width:1200px;display:flex;justify-content:center;gap:15px}
.social span{width:28px;height:28px;border-radius:50%;background:var(--olive)}
.rule{left:111px;top:2993px;width:978px;height:1px;background:#8a8f88}
.legal{top:3013px;font-size:13.5px}
</style>
</head>
<body>
<div class="abs hero"></div>
<div class="abs face" role="img" aria-label="Illustrated portrait of the creature in green ink"></div>
<svg class="abs hero-edge" width="1200" height="60" viewBox="0 0 1200 60" aria-hidden="true"><path d="M0 30 L40 22 L80 34 L130 24 L190 36 L250 26 L320 38 L380 28 L440 40 L510 30 L580 38 L650 27 L720 37 L790 29 L860 39 L930 28 L1000 36 L1070 26 L1140 35 L1200 28 L1200 60 L0 60Z" fill="var(--bg)"/></svg>

<div class="abs logo" style="left:110px;top:36px">Galvanica</div>
<nav class="abs nav">
  <a class="active">Home</a><a>About me</a><a>Our offer</a><a>Gallery</a><a>FAQ</a><a>Contact us</a>
</nav>
<div class="abs lang"><span class="dot"></span>ENG
  <svg width="9" height="6" viewBox="0 0 9 6"><path d="M1 1l3.5 3.5L8 1" stroke="#fff" stroke-width="1.6" fill="none"/></svg></div>

<div class="abs lettering" role="img" aria-label="Hand-lettered show title: Galvanica, the rock opera"></div>
<p class="abs hero-text">Lorem ipsum dolor sit amet, consectetur adipiscing elit, sed do eiusmod tempor incididunt ut labore et dolore magna aliqua. Ut enim ad minim veniam, quis nostrud exercitation ullamco</p>
<div class="abs btn-green">Get started</div>
<div class="abs dots"><span></span><span></span><span></span></div>

<div class="abs card" style="left:111px;top:735px">
  <div class="pic" role="img" aria-label="Ballet couple dancing on stage" style="background:linear-gradient(135deg,#4a3a2c,#201812 70%)"></div>
  <h3>Program and tickets</h3>
  <p>Lorem ipsum dolor sit amet, consectetur adipiscing elit, sed do eiusmod tempor incididunt ut labore et dolore magna aliqua. Ut enim ad minim</p>
  <div class="more">LEARN MORE <svg width="13" height="13" viewBox="0 0 13 13"><circle cx="6.5" cy="6.5" r="6.5" fill="#fff"/><path d="M4 6.5h5M6.8 4.2l2.3 2.3-2.3 2.3" stroke="#6c7a58" stroke-width="1.6" fill="none"/></svg></div>
</div>
<div class="abs card" style="left:445px;top:735px">
  <div class="pic" role="img" aria-label="Ballerinas performing under blue stage light" style="background:linear-gradient(180deg,#1a4fb0,#38a0e8 55%,#0d1a3a)"></div>
  <h3>Our offer</h3>
  <p>Lorem ipsum dolor sit amet, consectetur adipiscing elit, sed do eiusmod tempor incididunt ut labore et dolore magna aliqua. Ut enim ad minim</p>
  <div class="more">LEARN MORE <svg width="13" height="13" viewBox="0 0 13 13"><circle cx="6.5" cy="6.5" r="6.5" fill="#fff"/><path d="M4 6.5h5M6.8 4.2l2.3 2.3-2.3 2.3" stroke="#6c7a58" stroke-width="1.6" fill="none"/></svg></div>
</div>
<div class="abs card" style="left:779px;top:735px">
  <div class="pic" role="img" aria-label="Concert crowd seen from behind" style="background:linear-gradient(180deg,#4b4d5a,#1d1c22 60%)"></div>
  <h3>Supporters</h3>
  <p>Lorem ipsum dolor sit amet, consectetur adipiscing elit, sed do eiusmod tempor incididunt ut labore et dolore magna aliqua. Ut enim ad minim</p>
  <div class="more">LEARN MORE <svg width="13" height="13" viewBox="0 0 13 13"><circle cx="6.5" cy="6.5" r="6.5" fill="#fff"/><path d="M4 6.5h5M6.8 4.2l2.3 2.3-2.3 2.3" stroke="#6c7a58" stroke-width="1.6" fill="none"/></svg></div>
</div>

<div class="abs band" role="img" aria-label="Faded city skyline in green tint"></div>
<svg class="abs" style="left:626px;top:1217px" width="18" height="505" viewBox="0 0 18 505" aria-hidden="true"><path d="M18 0V21H0Z" fill="#fff"/><path d="M18 505V482H0Z" fill="#fff"/></svg>
<div class="abs singer" role="img" aria-label="Singer with microphone in stage smoke and blue light"></div>
<div class="abs about" style="left:111px;top:1322px;width:466px">
  <h2>About me</h2>
  <p>Lorem ipsum dolor sit amet, consectetur adipiscing elit, sed do eiusmod tempor incididunt ut labore et dolore magna aliqua. Ut enim ad minim veniam, quis nostrud exercitation ullamco laboris nisi ut aliquip ex ea commodo consequat. Duis aute irure dolor in reprehenderit in voluptate velit esse cillum dolore eu fugiat nulla pariatur. Excepteur sint occaecat cupidatat non proident, sunt in culpa qui officia deserunt mollit anim id est laborum.</p>
</div>
<div class="abs btn-white">Learn more</div>

<h2 class="abs section-title" style="top:1805px">Latest news</h2>
<div class="abs news" style="left:111px;top:1877px">
  <div class="pic" role="img" aria-label="Aerial silk performer in purple light" style="background:linear-gradient(135deg,#3a0f3a,#a03ca8 50%,#2a0a2a)"></div>
  <div class="body"><h4>Lorem ipsum dolor sit amet, consectetur adipiscing</h4>
  <div class="date"><svg width="12" height="12" viewBox="0 0 12 12"><rect x="1" y="2" width="10" height="9" fill="none" stroke="#6c7a58" stroke-width="1.5"/><path d="M1 5h10M4 1v2M8 1v2" stroke="#6c7a58" stroke-width="1.5"/></svg>Jan 20, 2021</div>
  <p>Lorem ipsum dolor sit amet, cons ectetur adipiscing elit, sed do eiu sm od tempor incididunt</p></div>
</div>
<div class="abs news" style="left:612px;top:1877px">
  <div class="pic" role="img" aria-label="Performer in top hat on dark stage" style="background:linear-gradient(135deg,#2a1a22,#3b3038 50%,#141014)"></div>
  <div class="body"><h4>Lorem ipsum dolor sit amet, consectetur adipiscing</h4>
  <div class="date"><svg width="12" height="12" viewBox="0 0 12 12"><rect x="1" y="2" width="10" height="9" fill="none" stroke="#6c7a58" stroke-width="1.5"/><path d="M1 5h10M4 1v2M8 1v2" stroke="#6c7a58" stroke-width="1.5"/></svg>Jan 20, 2021</div>
  <p>Lorem ipsum dolor sit amet, cons ectetur adipiscing elit, sed do eiu sm od tempor incididunt</p></div>
</div>
<div class="abs news" style="left:111px;top:2127px">
  <div class="pic" role="img" aria-label="Singer among string lights" style="background:radial-gradient(circle at 60% 30%,#6a5a30,#2a2010 60%,#120e08)"></div>
  <div class="body"><h4>Lorem ipsum dolor sit amet, consectetur adipiscing</h4>
  <div class="date"><svg width="12" height="12" viewBox="0 0 12 12"><rect x="1" y="2" width="10" height="9" fill="none" stroke="#6c7a58" stroke-width="1.5"/><path d="M1 5h10M4 1v2M8 1v2" stroke="#6c7a58" stroke-width="1.5"/></svg>Jan 20, 2021</div>
  <p>Lorem ipsum dolor sit amet, cons ectetur adipiscing elit, sed do eiu sm od tempor incididunt</p></div>
</div>
<div class="abs news" style="left:612px;top:2127px">
  <div class="pic" role="img" aria-label="Stage scene with flames and performers" style="background:linear-gradient(135deg,#5a2a14,#3a2418 50%,#1a1210)"></div>
  <div class="body"><h4>Lorem ipsum dolor sit amet, consectetur adipiscing</h4>
  <div class="date"><svg width="12" height="12" viewBox="0 0 12 12"><rect x="1" y="2" width="10" height="9" fill="none" stroke="#6c7a58" stroke-width="1.5"/><path d="M1 5h10M4 1v2M8 1v2" stroke="#6c7a58" stroke-width="1.5"/></svg>Jan 20, 2021</div>
  <p>Lorem ipsum dolor sit amet, cons ectetur adipiscing elit, sed do eiu sm od tempor incididunt</p></div>
</div>

<h2 class="abs section-title" style="top:2442px">Our gallery</h2>
<div class="abs strip" style="left:0;width:240px;background:linear-gradient(135deg,#3a3a3a,#1e1e1e)" role="img" aria-label="Black and white singer with microphone"></div>
<div class="abs strip" style="left:240px;width:220px;background:linear-gradient(135deg,#6a5a50,#2a2220)" role="img" aria-label="Singer with decorated glasses"></div>
<div class="abs" style="left:460px;top:2519px;width:280px;height:246px;background:radial-gradient(circle at 55% 40%,#4a3aa0,#24185a 60%,#120c30)" role="img" aria-label="Performer under purple stage light"></div>
<div class="abs strip" style="left:740px;width:220px;background:linear-gradient(135deg,#2a1a5a,#120a2a)" role="img" aria-label="Guitarist in violet light"></div>
<div class="abs strip" style="left:960px;width:240px;background:linear-gradient(135deg,#4a1a1e,#2a0e12)" role="img" aria-label="Singer in hat under red light"></div>
<svg class="abs arrow" style="left:51px" width="12" height="18" viewBox="0 0 12 18" aria-hidden="true"><path d="M9 2L3 9l6 7" stroke="#fff" stroke-width="2.5" fill="none"/></svg>
<svg class="abs arrow" style="left:1139px" width="12" height="18" viewBox="0 0 12 18" aria-hidden="true"><path d="M3 2l6 7-6 7" stroke="#fff" stroke-width="2.5" fill="none"/></svg>

<div class="abs logo" style="left:0;top:2820px;width:1200px;text-align:center">Galvanica</div>
<nav class="abs footer-nav"><span>Home</span><span>About me</span><span>Our offer</span><span>Gallery</span><span>Contact</span><span>FAQ</span></nav>
<div class="abs social"><span></span><span></span><span></span><span></span></div>
<div class="abs rule"></div>
<div class="abs legal" style="left:111px">Terms &amp; Conditions &nbsp;&nbsp;| &nbsp;&nbsp;Privacy policy &nbsp;&nbsp;| &nbsp;&nbsp;Terms &nbsp;&amp; conditions of sales</div>
<div class="abs legal" style="right:111px">© &nbsp;Copyrights 2021 Company name | All Rights Reserved</div>
</body>
</html>
```